Business Card Design needed for start up company Halvora

In need of a new business card designed for a start up company based in Sydney, Halvora is a new start up innovative Company, our mission it to make property accessible for everyday Australian and to become the leading Real Estate platform in Australia. We want it to be fresh and clean.

Industry/Entity Type

Financial

Contact Information for Business Card

Section for Name
Section for Title

HALVORA - The Strength of Pooling
Mobile:
Direct:

Font styles to use
Sans Serif

Colors
33a6d7
0692cd
0255a3
ffffff

Requirements
Must have
• Logo, all business card details

```html
<!DOCTYPE html>
<html lang="en">
<head>
<meta charset="utf-8">
<title>Halvora Business Card</title>
<link rel="stylesheet" href="https://fonts.googleapis.com/css2?family=Open+Sans:wght@400;600;700&display=swap">
<style>
  :root {
    --navy: #1e3f76;
    --sky: #2a9bd6;
    --white: #ffffff;
    --backdrop: #eceef1;
    --body-font: "Open Sans", sans-serif;
  }
  html, body {
    margin: 0;
    width: 1200px;
    height: 900px;
    overflow: hidden;
    background: var(--backdrop);
  }
  .stage { position: relative; width: 1200px; height: 900px; }
  .card { position: absolute; box-shadow: 0 6px 18px rgba(0,0,0,0.18); overflow: hidden; }

  .card-front { left: 77px; top: 33px; width: 589px; height: 365px; background: var(--white); }
  .card-front .bands { position: absolute; inset: 0; }

  .brand-name {
    position: absolute;
    margin: 0;
    font-family: var(--body-font);
    font-weight: 700;
    letter-spacing: 1px;
    line-height: 1;
    white-space: nowrap;
    transform: translate(-50%, -50%);
  }
  .card-front .brand-name { left: 295px; top: 94px; font-size: 62px; color: var(--navy); }

  .contact-list {
    position: absolute; left: 30px; top: 260px; margin: 0; padding: 0; list-style: none;
    font-family: var(--body-font); font-size: 15px; color: var(--white);
  }
  .contact-list li { display: flex; align-items: center; gap: 8px; height: 21px; }
  .contact-list svg { width: 12px; height: 12px; flex: none; }

  .holder { position: absolute; right: 35px; top: 260px; text-align: right; font-family: var(--body-font); color: var(--white); }
  .holder-name { font-size: 24px; font-weight: 400; line-height: 1.1; margin: 0; }
  .holder-title { font-size: 15px; margin: 2px 0 0; }

  .card-back { left: 388px; top: 505px; width: 567px; height: 352px; background: var(--navy); }
  .card-back .brand-name { left: 284px; top: 176px; font-size: 66px; color: var(--white); }
  .tagline {
    position: absolute; left: 0; right: 0; top: 250px; margin: 0; text-align: center;
    font-family: var(--body-font); font-weight: 600; font-size: 16px; color: var(--white);
  }
</style>
</head>
<body>
<main class="stage">
  <section class="card card-front">
    <svg class="bands" width="589" height="365" viewBox="0 0 589 365" aria-hidden="true">
      <polygon fill="var(--sky)" points="0,190 398,190 380,216 0,216"/>
      <polygon fill="var(--navy)" points="0,217 385,217 413,180 589,180 589,365 0,365"/>
    </svg>
    <p class="brand-name">HALVORA</p>
    <ul class="contact-list">
      <li>
        <svg viewBox="0 0 12 12"><rect x="3" y="0.5" width="6" height="11" rx="1" fill="none" stroke="currentColor" stroke-width="1.2"/><rect x="5" y="9" width="2" height="1" fill="currentColor"/></svg>
        044-987 654 321
      </li>
      <li>
        <svg viewBox="0 0 12 12"><path d="M1 4 Q6 0 11 4 L10 5.5 L8 4.5 L8 3.5 Q6 3 4 3.5 L4 4.5 L2 5.5 Z" fill="currentColor"/><rect x="2" y="6" width="8" height="5" rx="1" fill="currentColor"/></svg>
        044-987 654 321
      </li>
      <li>
        <svg viewBox="0 0 12 12"><rect x="0.5" y="2" width="11" height="8" fill="currentColor"/><path d="M0.5 2 L6 6.5 L11.5 2" fill="none" stroke="var(--navy)" stroke-width="1"/></svg>
        hello@halvora.com
      </li>
    </ul>
    <div class="holder">
      <p class="holder-name">Marcus Ellery</p>
      <p class="holder-title">Managing Director</p>
    </div>
  </section>

  <section class="card card-back">
    <p class="brand-name">HALVORA</p>
    <p class="tagline">THE STRENGTH OF POOLING</p>
  </section>
</main>
</body>
</html>
```